BRELWINCare.co.uk - Mental Health Clinic for Child and Adolescents

Updated 29/01/2018***
I am not sure you guys are getting the idea regards to the opening page / homescreen layout. Can you look at the new images I have uploaded (page 5, 6 and 7) These are some of the layouts I like but to incorporate my chosen images, with the BRELWIN commissioner, buttons and a sliding header bar.
I have written a strong brief, I am looking for a website, preferably wordpress as i know they are easy to maintain. I am looking for a one page site, with the top / opening page being full screen image with drop down categories. I have made a rough design, see full brief in word doc attached, there is some freedom to play around with the design aspect but it will need to relay all the content provided. I like a minimal feel. I have also attached some images that may be useful, but will need a new logo for BRELWIN Care. I have attached some logo idea's, it is up to you decide whether you want to use them.
I would prefer the homepage as full screen image, and the categories offered as a drop down or over the main image.
I have also attached linked to some competitors websites:
https://www.vorimant-health.co.uk/
http://www.qlbn.org.uk/
Industry/Entity Type
Clinic
Number of Pages Required
1 page
Font styles to use
Look and feel
Each slider illustrates characteristics of the customer's brand and the style your logo design should communicate.

```html
<!DOCTYPE html>
<html lang="en">
<head>
<meta charset="utf-8">
<title>BRELWIN Care – ADHD Services</title>
<link href="https://fonts.googleapis.com/css2?family=Open+Sans:wght@400;600&family=Poppins:wght@400;500;600&display=swap" rel="stylesheet">
<style>
  :root {
    --page-bg: #efeeee;
    --white: #ffffff;
    --ink: #1c1c1c;
    --body-ink: #2a2a2a;
    --teal: #12937a;
    --purple: #4b1769;
    --rule: #dcdcdc;
    --icon: #222222;
  }
  * { box-sizing: border-box; margin: 0; padding: 0; }
  html, body { width: 1200px; height: 600px; overflow: hidden; }
  body { background: var(--page-bg); font-family: "Open Sans", sans-serif; color: var(--ink); }

  .canvas { position: relative; width: 1200px; height: 600px; overflow: hidden; background: var(--page-bg); }

  .brand {
    position: absolute; left: 0; top: 0; width: 155px; height: 85px;
    background: var(--white); z-index: 3;
    display: flex; flex-direction: column; justify-content: center; padding-left: 8px;
  }
  .brand-name {
    font-family: "Poppins", sans-serif; font-weight: 600; font-size: 22px;
    color: var(--purple); line-height: 1; letter-spacing: 0.5px; padding-left: 10px;
  }
  .brand-tagline {
    font-family: "Poppins", sans-serif; font-weight: 600; font-size: 9.5px;
    color: var(--purple); margin-top: 8px;
  }

  .side-nav {
    position: absolute; left: 0; top: 85px; width: 65px; height: 515px;
    background: var(--white); z-index: 2;
  }
  .nav-item {
    position: absolute; left: 0; width: 65px;
    display: flex; align-items: center; justify-content: center;
    border-bottom: 1px solid var(--rule);
  }
  .nav-item svg { width: 30px; height: 30px; }
  .nav-item--active {
    width: 155px; background: var(--teal); border-right: 3px solid #111;
    justify-content: flex-start; padding-left: 16px; gap: 24px; border-bottom: none;
  }
  .nav-label { font-family: "Poppins", sans-serif; font-size: 14px; color: var(--white); letter-spacing: 0.3px; }

  .content { position: absolute; left: 246px; top: 84px; width: 560px; }
  .page-title { font-family: Arial, Helvetica, sans-serif; font-weight: 400; font-size: 36px; line-height: 1; color: #111; }
  .intro {
    margin-top: 14px; font-size: 12.4px; line-height: 29px; color: var(--body-ink);
    text-align: justify;
  }
  .services-heading { margin-top: 26px; font-weight: 600; font-size: 19.5px; color: var(--teal); }
  .service-list { list-style: none; margin-top: 16px; }
  .service-list li {
    display: flex; align-items: center; gap: 12px; height: 34.5px;
    font-family: "Poppins", sans-serif; font-size: 14.5px; color: #222;
  }
  .service-list svg { width: 7px; height: 16px; }

  .footer-note {
    position: absolute; left: 0; right: 0; top: 569px; padding-left: 2px;
    text-align: center; font-family: "Poppins", sans-serif; font-size: 11px; color: #222;
  }

  .hero-photo { position: absolute; left: 0; top: 0; width: 1200px; height: 600px; z-index: 1; pointer-events: none; }
</style>
</head>
<body>
<div class="canvas">

  <svg class="hero-photo" viewBox="0 0 1200 600" role="img" aria-label="Photo of three smiling teenagers sitting together on a sofa against a white brick wall">
    <defs>
      <linearGradient id="photoTone" x1="0" y1="0" x2="0" y2="1">
        <stop offset="0" stop-color="#e9e8e6"/>
        <stop offset="0.45" stop-color="#b9b3ad"/>
        <stop offset="0.8" stop-color="#6f8aa6"/>
        <stop offset="1" stop-color="#6b7f7a"/>
      </linearGradient>
      <linearGradient id="edgeStroke" x1="0" y1="0" x2="0" y2="1">
        <stop offset="0" stop-color="#4b1769"/>
        <stop offset="0.55" stop-color="#3a2a70"/>
        <stop offset="1" stop-color="#12937a"/>
      </linearGradient>
    </defs>
    <path d="M1200,62 L870,140 Q834,150 840,186 L926,452 Q944,480 978,492 L1200,570 Z" fill="url(#photoTone)"/>
    <path d="M1200,60 L870,138 Q834,148 840,186 L926,452" fill="none" stroke="url(#edgeStroke)" stroke-width="6" stroke-linecap="round"/>
  </svg>

  <header class="brand">
    <div class="brand-name">BRELWIN</div>
    <div class="brand-tagline">Child &amp; Adolescent Clinic</div>
  </header>

  <nav class="side-nav" aria-label="Main">
    <div class="nav-item" style="top:0;height:88px;">
      <svg viewBox="0 0 30 30"><path d="M3 8h24M3 15h24M3 22h24" stroke="var(--icon)" stroke-width="2" fill="none"/></svg>
    </div>
    <div class="nav-item" style="top:88px;height:75px;">
      <svg viewBox="0 0 30 30" fill="none" stroke="var(--icon)" stroke-width="1.4"><rect x="5" y="5" width="18" height="21"/><path d="M8 3v4M12 3v4M16 3v4M20 3v4M8 12h8M8 16h6M8 20h5"/><path d="M26 9l-9 11-2 4 4-2 9-11z"/></svg>
    </div>
    <div class="nav-item" style="top:163px;height:75px;">
      <svg viewBox="0 0 30 30" fill="none" stroke="var(--icon)" stroke-width="1.4"><circle cx="15" cy="10" r="4.5"/><circle cx="7" cy="14" r="3.5"/><circle cx="23" cy="14" r="3.5"/><path d="M8 27v-4a7 7 0 0 1 14 0v4M2 27v-3a5 5 0 0 1 5-5M28 27v-3a5 5 0 0 0-5-5"/></svg>
    </div>
    <div class="nav-item nav-item--active" style="top:238px;height:74px;">
      <svg viewBox="0 0 30 30" fill="none" stroke="var(--white)" stroke-width="1.5"><path d="M4 22L22 4l4 4L8 26H4z"/><path d="M19 7l4 4M4 8l4-4 18 18-4 4z"/><path d="M11 11l2-2M15 15l2-2M19 19l2-2"/></svg>
      <span class="nav-label">SERVICES</span>
    </div>
    <div class="nav-item" style="top:312px;height:75px;">
      <svg viewBox="0 0 30 30" fill="none" stroke="var(--icon)" stroke-width="1.4"><path d="M8 4l4 5-2.5 3a14 14 0 0 0 8.5 8.5l3-2.5 5 4-2.5 4C14 26 4 16 4 6.5z"/></svg>
    </div>
    <div class="nav-item" style="top:387px;height:80px;">
      <svg viewBox="0 0 30 30" fill="none" stroke="var(--icon)" stroke-width="1.4"><rect x="4" y="4" width="22" height="22"/><path d="M4 10h22M4 17h22M7 7h10M7 13h14M8 20h5v4H8zM16 21h7M16 23h5"/></svg>
    </div>
  </nav>

  <main class="content">
    <h1 class="page-title">Adhd</h1>
    <p class="intro">We have a multidisciplinaryteam that has been selected due to their vast experience and repu&shy;tation of being some of the best in their field. The team consists of a Clinical Psychologist, Con&shy;sultant Psychiatrist and Nurse who will work collaboratively to provide a robust, thorough and highly accurate assessment.&nbsp; Should your child need post treatment, we will recommend and offer support that is best suited to the child and family.</p>
    <h2 class="services-heading">Services offered are:</h2>
    <ul class="service-list">
      <li><svg viewBox="0 0 7 16"><path d="M1 1h5v11l-2.5 3.5L1 12z" fill="none" stroke="#333" stroke-width="1.2"/><path d="M1 4h5" stroke="#333"/></svg>Service 1</li>
      <li><svg viewBox="0 0 7 16"><path d="M1 1h5v11l-2.5 3.5L1 12z" fill="none" stroke="#333" stroke-width="1.2"/><path d="M1 4h5" stroke="#333"/></svg>Service 2</li>
      <li><svg viewBox="0 0 7 16"><path d="M1 1h5v11l-2.5 3.5L1 12z" fill="none" stroke="#333" stroke-width="1.2"/><path d="M1 4h5" stroke="#333"/></svg>Service 3</li>
      <li><svg viewBox="0 0 7 16"><path d="M1 1h5v11l-2.5 3.5L1 12z" fill="none" stroke="#333" stroke-width="1.2"/><path d="M1 4h5" stroke="#333"/></svg>Service 4</li>
      <li><svg viewBox="0 0 7 16"><path d="M1 1h5v11l-2.5 3.5L1 12z" fill="none" stroke="#333" stroke-width="1.2"/><path d="M1 4h5" stroke="#333"/></svg>Service 5</li>
      <li><svg viewBox="0 0 7 16"><path d="M1 1h5v11l-2.5 3.5L1 12z" fill="none" stroke="#333" stroke-width="1.2"/><path d="M1 4h5" stroke="#333"/></svg>Service 6</li>
    </ul>
  </main>

  <footer class="footer-note">© 2018 All Rights Reserved.brelwin.com</footer>
</div>
</body>
</html>
```